Rollway Stays

We are 100% online, promoting accommodation details and booking facilities for wheelchair dependant travellers.
Listings will only be accommodation providers which meet our specific criteria.

Target Market(s)

Wheelchair dependant people and their companions

Industry/Entity Type

Accommodation

Contact Information for Business Card

Name, mobile phone number, email address, website address

```html
<!DOCTYPE html>
<html lang="en">
<head>
<meta charset="utf-8">
<title>Rollway Stays – Business Card</title>
<link rel="stylesheet" href="https://fonts.googleapis.com/css2?family=Open+Sans:wght@400;600;700&display=swap">
<style>
  :root {
    --page-bg: #7d8591;
    --card-dark: #363435;
    --card-dark-edge: #2b2a2b;
    --card-light: #f7f7f7;
    --card-light-edge: #ececec;
    --brand-red: #e0183a;
    --ink: #2c2b2c;
    --ink-soft: #3d3c3d;
  }
  * { box-sizing: border-box; margin: 0; padding: 0; }
  html, body { width: 1200px; height: 1024px; overflow: hidden; }
  body {
    background: var(--page-bg);
    font-family: "Open Sans", Arial, sans-serif;
    display: flex;
    flex-direction: column;
    align-items: center;
    justify-content: center;
    gap: 56px;
  }
  .card {
    position: relative;
    width: 760px;
    height: 434px;
    border-radius: 26px;
    overflow: hidden;
    box-shadow: 0 10px 28px rgba(0,0,0,0.25);
  }
  /* Front */
  .card--front {
    background: radial-gradient(ellipse at 60% 40%, var(--card-dark) 0%, var(--card-dark-edge) 100%);
  }
  .brand {
    display: flex;
    align-items: center;
    gap: 14px;
    color: var(--brand-red);
    font-weight: 700;
    letter-spacing: -0.5px;
  }
  .brand__dot {
    width: 22px; height: 22px;
    border-radius: 50%;
    background: var(--brand-red);
    flex: none;
  }
  .card--front .brand {
    position: absolute;
    left: 330px; top: 172px;
    font-size: 56px;
  }
  .front__url {
    position: absolute;
    left: 48px; bottom: 40px;
    color: var(--brand-red);
    font-size: 17px;
    letter-spacing: 0.3px;
  }
  /* Back */
  .card--back {
    background: linear-gradient(135deg, #ffffff 0%, var(--card-light) 50%, var(--card-light-edge) 100%);
  }
  .back__stripe {
    position: absolute;
    left: 0; top: 0; bottom: 0;
    width: 22px;
    background: linear-gradient(to bottom, var(--ink) 0 60%, var(--brand-red) 60% 100%);
  }
  .contact {
    position: absolute;
    left: 78px; top: 70px;
  }
  .contact__name {
    font-size: 27px;
    font-weight: 700;
    color: var(--ink);
    margin-bottom: 24px;
  }
  .contact__list { list-style: none; }
  .contact__item {
    display: flex;
    align-items: center;
    gap: 12px;
    font-size: 18px;
    color: var(--ink-soft);
    line-height: 1.65;
  }
  .contact__icon { width: 13px; height: 13px; flex: none; }
  .card--back .brand {
    position: absolute;
    right: 60px; bottom: 64px;
    font-size: 50px;
  }
</style>
</head>
<body>

  <section class="card card--front" aria-label="Card front">
    <div class="brand">
      <span class="brand__dot"></span>
      <span class="brand__name">Rollway Stays</span>
    </div>
    <p class="front__url">www.rollwaystays.com.au</p>
  </section>

  <section class="card card--back" aria-label="Card back">
    <div class="back__stripe"></div>
    <div class="contact">
      <h1 class="contact__name">Alex Morgan</h1>
      <ul class="contact__list">
        <li class="contact__item">
          <svg class="contact__icon" viewBox="0 0 13 13" aria-hidden="true">
            <rect x="3" y="0.5" width="7" height="12" rx="1.5" fill="none" stroke="#e0183a" stroke-width="1.4"/>
            <rect x="5.5" y="10" width="2" height="1.2" fill="#e0183a"/>
          </svg>
          123-555-0147
        </li>
        <li class="contact__item">
          <svg class="contact__icon" viewBox="0 0 13 13" aria-hidden="true">
            <rect x="0.7" y="2.5" width="11.6" height="8" fill="none" stroke="#e0183a" stroke-width="1.4"/>
            <path d="M1 3l5.5 4.2L12 3" fill="none" stroke="#e0183a" stroke-width="1.4"/>
          </svg>
          info@rollwaystays.com.au
        </li>
        <li class="contact__item">
          <svg class="contact__icon" viewBox="0 0 13 13" aria-hidden="true">
            <circle cx="6.5" cy="6.5" r="5.8" fill="none" stroke="#e0183a" stroke-width="1.3"/>
            <ellipse cx="6.5" cy="6.5" rx="2.6" ry="5.8" fill="none" stroke="#e0183a" stroke-width="1.1"/>
            <path d="M0.8 6.5h11.4" stroke="#e0183a" stroke-width="1.1"/>
          </svg>
          www.rollwaystays.com.au
        </li>
      </ul>
    </div>
    <div class="brand">
      <span class="brand__dot"></span>
      <span class="brand__name">Rollway Stays</span>
    </div>
  </section>

</body>
</html>
```